Service Menu refresh 2018 Update of menu pricing

We currently have service menus as attached. We will be updating our look via our homepage image, our service menu and our in-house beverage and treatment menu.
We are a natural and sustainable hair salon group and moving more towards head spa which consists of treatments, beauty, tanning as well as your traditional hair services. Our imagery needs to reflect our efforts in spa treatments in the hair and scalp area and use natural materials and colours reflecting sustainability.
Velune is the brand we stock and promote.

Target Market(s)

Men or women interesting in personal maintenance with natural and organic products and using sustainable practises

Industry/Entity Type

Hair And Beauty

Font styles to use
Sans Serif
Other font styles liked:
• Arial or Helvetica

Colors
9acb3c
abd037
cadf82
ffffff

Requirements
Must have
• Name on the front cover, locations on back cover
Nice to have
• Prestige feel, reflect male and female clients
Should not have
• Bold artificial writing or any type of cartoon images.
• Same images as existing menu.

```html
<!DOCTYPE html>
<html lang="en">
<head>
<meta charset="utf-8">
<title>Leafwell Hair Salons – Service Menu</title>
<link href="https://fonts.googleapis.com/css2?family=Montserrat:wght@400;500;600;700&display=swap" rel="stylesheet">
<style>
  :root{
    --bg:#e9e6e1;
    --paper:#ffffff;
    --ink:#333333;
    --ink-soft:#555555;
    --head-grey:#8d8d8d;
    --rule:#d4d4d4;
    --row-alt:#f1f1f1;
    --lime:#c8df74;
    --leaf:#9acb3c;
    --photo-dark:#2a2620;
    --photo-mid:#4b4a3a;
    --foliage:#5fa578;
    --foliage-deep:#2f6b45;
  }
  *{box-sizing:border-box;margin:0;padding:0}
  html,body{width:1200px;height:903px;overflow:hidden;background:var(--bg)}
  body{font-family:"Montserrat",Arial,sans-serif;color:var(--ink);position:relative}

  .card-slot{position:absolute;left:220px;width:760px;height:419px;overflow:hidden;box-shadow:0 2px 8px rgba(0,0,0,.12)}
  .card-slot--front{top:24px}
  .card-slot--back{top:460px}
  .card{position:absolute;top:0;left:0;width:803px;height:443px;transform:scale(.9465);transform-origin:0 0;background:var(--paper);overflow:hidden}

  /* front */
  .cover-photo{position:absolute;inset:0;background:
      radial-gradient(ellipse 150px 220px at 520px 300px,#6b3a24 0%,rgba(107,58,36,0) 70%),
      radial-gradient(ellipse 260px 200px at 200px 160px,#6f6f60 0%,rgba(111,111,96,0) 75%),
      linear-gradient(160deg,var(--photo-mid) 0%,var(--photo-dark) 70%)}
  .cover-foliage{position:absolute;right:0;top:0;width:330px;height:443px;
      background:linear-gradient(200deg,var(--foliage) 0%,var(--foliage-deep) 60%,#3c8757 100%);
      clip-path:polygon(30% 0,100% 0,100% 100%,0 100%,22% 70%,40% 40%)}
  .brand{position:absolute;left:150px;top:58px;display:flex;align-items:center;gap:14px}
  .brand-dot{width:44px;height:44px;border-radius:50%;background:var(--leaf)}
  .brand-name{font-size:28px;font-weight:500;color:#ffffff;letter-spacing:.2px;line-height:1}
  .cover-url{position:absolute;left:34px;top:374px;font-size:13px;color:#ffffff;letter-spacing:1px}

  /* back */
  .price-table{position:absolute;top:25px;border:1px solid var(--rule);border-radius:4px;overflow:hidden;border-collapse:separate;border-spacing:0;table-layout:fixed;font-size:8.4px;background:var(--paper)}
  .price-table--cuts{left:31px;width:344px}
  .price-table--colour{left:388px;width:383px}
  .price-table th{background:var(--head-grey);color:#fff;font-weight:600;font-size:12px;height:23px;border-left:1px solid #fff}
  .price-table th:first-child{border-left:none}
  .section td{background:var(--lime);color:var(--ink);font-size:12.5px;font-weight:500;height:20px;line-height:18px;padding:0 0 0 18px;letter-spacing:.3px;border-top:2px solid #fff}
  .price-table--colour .section td{padding-left:10px}
  .group td{vertical-align:top;padding:2px 0 0 0;line-height:12.6px;border-left:1px solid var(--rule);border-top:2px solid #fff}
  .group td:first-child{border-left:none;padding-left:18px}
  .price-table--colour .group td:first-child{padding-left:10px}
  .group--alt td{background:var(--row-alt)}
  .group td.price{padding-left:11px;color:var(--ink-soft)}
  .group--ladies td{height:54px}
  .group--mens td{height:46px;padding-top:6px}
  .group--children td{height:72px;padding-top:5px}
  .group--blowdry td{height:33px;padding-top:4px}
  .group--treat td{height:29px;padding-top:2px}
  .group--upstyle td{height:35px;padding-top:6px}
  .group--colour td{height:65px;padding-top:4px}
  .group--nectar td{height:42px;padding-top:10px}
  .group--foils td{height:65px;padding-top:6px}
  .group--straight td{height:79px;padding-top:10px}
  .item-title{font-weight:700;font-size:8px;letter-spacing:.3px}
  .item{color:var(--ink-soft)}
  .note{font-size:8px;color:var(--ink-soft)}
  .cover-foot{position:absolute;left:0;right:0;top:398px;text-align:center;font-size:8.2px;line-height:12px;color:var(--ink-soft)}
</style>
</head>
<body>

<div class="card-slot card-slot--front">
  <section class="card card--front">
    <div class="cover-photo" role="img" aria-label="Photograph of a woman in a wide-brim hat and sunglasses with long auburn hair, standing in a greenhouse"></div>
    <div class="cover-foliage" role="img" aria-label="Illustration of lush tropical leaves and ferns in shades of green"></div>
    <div class="brand">
      <span class="brand-dot"></span>
      <span class="brand-name">leafwell hair salons</span>
    </div>
    <p class="cover-url">www.leafwellhair.com.au</p>
  </section>
</div>

<div class="card-slot card-slot--back">
  <section class="card card--back">

    <table class="price-table price-table--cuts">
      <colgroup><col style="width:150px"><col><col><col><col></colgroup>
      <thead><tr><th></th><th>S</th><th>M</th><th>L</th><th>XL</th></tr></thead>
      <tbody>
        <tr class="section"><td colspan="5">CUT &amp; BLOWDRY</td></tr>
        <tr class="group group--ladies">
          <td><span class="item-title">LADIES</span><br><span class="item-title">FRINGE</span><br><span class="item">Trim</span><br><span class="item">Restyle</span></td>
          <td class="price">$77<br><br>$25<br>$35</td>
          <td class="price">$88</td>
          <td class="price">$99</td>
          <td class="price">$110</td>
        </tr>
        <tr class="group group--alt group--mens">
          <td><span class="item-title">MENS</span><br><span class="item">Single clipper</span><br><span class="item">Style cut</span></td>
          <td class="price"><br>$28<br>$42</td><td></td><td></td><td></td>
        </tr>
        <tr class="group group--children">
          <td><span class="item-title">CHILDREN</span><br><span class="item">10 and under</span><br><span class="item">11-16 Male</span><br><span class="item">11-16 Female</span><br><span class="item">add a wash</span></td>
          <td class="price"><br>$24<br>$32<br>$48<br>$5</td><td></td><td></td><td></td>
        </tr>
        <tr class="group group--alt group--blowdry">
          <td><span class="item-title">BLOWDRY</span><br><span class="item">Shampoo &amp; dry off</span></td>
          <td class="price">$47<br>$25</td><td class="price">$57</td><td class="price">$67</td><td class="price">$77</td>
        </tr>
        <tr class="section"><td colspan="5">TREATMENTS</td></tr>
        <tr class="group group--treat">
          <td><span class="item">deep treatment</span><br><span class="item">Head.Spa ritual</span></td>
          <td class="price">$35<br>$65</td><td></td><td></td><td></td>
        </tr>
        <tr class="section"><td colspan="5">UPSTYLE</td></tr>
        <tr class="group group--alt group--upstyle">
          <td><span class="item">45 minutes</span><br><span class="item">60 minutes</span></td>
          <td class="price">$85<br>$120</td><td></td><td></td><td></td>
        </tr>
      </tbody>
    </table>

    <table class="price-table price-table--colour">
      <colgroup><col style="width:190px"><col><col><col><col></colgroup>
      <thead><tr><th></th><th>S</th><th>M</th><th>L</th><th>XL</th></tr></thead>
      <tbody>
        <tr class="section"><td colspan="5">COLOUR</td></tr>
        <tr class="group group--colour">
          <td><span class="item-title">REGROWTH</span><br><span class="item-title">FULL COLOUR TINT</span><br><span class="item-title">REGROWTH LIGHTENING*</span><br><span class="item-title">BALAYAG E/OMBRE*</span></td>
          <td class="price">$83<br>$125<br>$165</td>
          <td class="price"><br>$145<br>$189<br>$275</td>
          <td class="price"><br>$165<br>$209<br>$375</td>
          <td class="price"><br>$185<br>$229<br>$475</td>
        </tr>
        <tr class="section"><td colspan="5">NECTAR TINT</td></tr>
        <tr class="group group--alt group--nectar">
          <td><span class="item-title">REGROWTH</span><br><span class="item-title">FULL COLOUR TINT</span></td>
          <td class="price">$99<br>$155</td><td class="price"><br>$175</td><td class="price"><br>$195</td><td class="price"><br>$205</td>
        </tr>
        <tr class="section"><td colspan="5">FOILS*</td></tr>
        <tr class="group group--foils">
          <td><span class="item-title">SINGLE*</span><br><span class="item-title">1/4 HEAD</span><br><span class="item-title">1/2 HEAD</span><br><span class="item-title">FULL HEAD</span></td>
          <td class="price">$11<br>$135<br>$185<br>$235</td>
          <td class="price">$13<br>$155<br>$205<br>$265</td>
          <td class="price">$17<br>$175<br>$235<br>$315</td>
          <td class="price">$22<br>$195<br>$265<br>$355</td>
        </tr>
        <tr class="section"><td colspan="5">STRAIGHT</td></tr>
        <tr class="group group--alt group--straight">
          <td><span class="item-title">KERATIN STRAIGHTENING SYSTEM</span><br><br><span class="note">*Includes colour match &amp; toner</span><br><span class="note">*Minimum 6 foils without colour</span><br><span class="note">*Minimum charge on a Sunday is $40</span></td>
          <td class="price">$365</td>
          <td class="price">$445</td>
          <td class="price">$535</td>
          <td class="price">$565</td>
        </tr>
      </tbody>
    </table>

    <p class="cover-foot">Pricing is indicative of average products used and time taken for each service. You will ALWAYS receive a firm price after your consultation.<br>S to the jaw line I M to the collarbone I L to the bra strap I XL past bra strap</p>
  </section>
</div>

</body>
</html>
```